Telecommunications Company needs a business card design

We are looking for a sleek, professional and modern business card design based off our new logo. Will look at both light and dark options. On some designs please provide a small space for a QR code

Target Market(s)

B2B clients in Australia

Contact Information for Business Card

Name, Position, Brisbane (head) office, Phone number, email address, QR code (link to our website qlinetelecom.com.au

Colors
0054AA
0677BA
7BADD7
CADEEF
E8F1F8
0094D4
00A9DD
6FCCEA
C7EBF8
E9F6FB
00AB8E
00BBA5
67D7C9
C6EFE9
E9F9F6

```html
<!DOCTYPE html>
<html lang="en">
<head>
<meta charset="utf-8">
<title>Qline Telecom — Business Card</title>
<link rel="stylesheet" href="https://fonts.googleapis.com/css2?family=Lato:wght@400;700&family=Oswald:wght@600&display=swap">
<style>
  :root {
    --stage: #1c1d1f;
    --card: #111213;
    --band-top: #00A9DD;
    --band-bottom: #0677BA;
    --accent: #0094D4;
    --ink: #f2f4f6;
    --muted: #8d9399;
    --rule: #6b7075;
  }
  * { box-sizing: border-box; margin: 0; padding: 0; }
  html, body { width: 1200px; height: 900px; overflow: hidden; background: var(--stage); }
  .stage {
    width: 1200px; height: 900px;
    display: flex; flex-direction: column; align-items: center; justify-content: center; gap: 48px;
  }
  .card {
    position: relative;
    width: 640px; height: 366px;
    background: var(--card);
    box-shadow: 0 10px 28px rgba(0,0,0,.55);
    overflow: hidden;
  }
  .card__band {
    position: absolute; left: 0; right: 0; bottom: 0; height: 12px;
    background: linear-gradient(to bottom, var(--band-top), var(--band-bottom));
  }
  /* front */
  .brand {
    position: absolute; left: 0; right: 0; top: 150px;
    display: flex; align-items: center; justify-content: center; gap: 14px;
  }
  .brand__dot { width: 22px; height: 22px; border-radius: 50%; background: var(--accent); }
  .brand__name {
    font-family: "Lato", sans-serif; font-weight: 700;
    font-size: 34px; letter-spacing: 4px; color: var(--accent);
  }
  /* back */
  .person {
    position: absolute; right: 384px; top: 140px; text-align: right;
  }
  .person__name {
    font-family: "Oswald", sans-serif; font-weight: 600;
    font-size: 30px; line-height: 1; letter-spacing: .5px;
    color: var(--accent); text-transform: uppercase;
  }
  .person__role {
    margin-top: 6px;
    font-family: "Lato", sans-serif; font-size: 15px; color: var(--ink); letter-spacing: .5px;
  }
  .divider {
    position: absolute; left: 276px; top: 136px; width: 1px; height: 80px; background: var(--rule);
  }
  .contacts {
    position: absolute; left: 298px; top: 144px; list-style: none;
    font-family: "Lato", sans-serif; font-size: 15px; color: var(--ink); letter-spacing: .4px;
  }
  .contacts__item { display: flex; align-items: center; gap: 10px; height: 23px; }
  .contacts__icon { width: 15px; height: 15px; flex: none; }
  .address {
    position: absolute; left: 120px; top: 292px;
    font-family: "Lato", sans-serif; font-size: 16px; color: var(--ink); letter-spacing: .4px;
  }
</style>
</head>
<body>
<main class="stage">
  <section class="card card--front" aria-label="Card front">
    <div class="brand">
      <span class="brand__dot"></span>
      <span class="brand__name">QLINE TELECOM</span>
    </div>
    <div class="card__band"></div>
  </section>

  <section class="card card--back" aria-label="Card back">
    <div class="person">
      <p class="person__name">Daniel Harper</p>
      <p class="person__role">Managing Director</p>
    </div>
    <div class="divider"></div>
    <ul class="contacts">
      <li class="contacts__item">
        <svg class="contacts__icon" viewBox="0 0 24 24" fill="var(--accent)"><path d="M6.6 10.8a15.1 15.1 0 0 0 6.6 6.6l2.2-2.2a1 1 0 0 1 1-.25 11.4 11.4 0 0 0 3.6.57 1 1 0 0 1 1 1V20a1 1 0 0 1-1 1A17 17 0 0 1 3 4a1 1 0 0 1 1-1h3.5a1 1 0 0 1 1 1c0 1.25.2 2.45.57 3.57a1 1 0 0 1-.25 1z"/></svg>
        <span>07 3100 2458</span>
      </li>
      <li class="contacts__item">
        <svg class="contacts__icon" viewBox="0 0 24 24" fill="none" stroke="var(--accent)" stroke-width="2.2"><rect x="2" y="5" width="20" height="14"/><path d="M2 5l10 8 10-8"/></svg>
        <span>info@qlinetelecom.com.au</span>
      </li>
      <li class="contacts__item">
        <svg class="contacts__icon" viewBox="0 0 24 24" fill="none" stroke="var(--accent)" stroke-width="2"><circle cx="12" cy="12" r="10"/><path d="M2 12h20M12 2c3 3 3 17 0 20M12 2c-3 3-3 17 0 20"/></svg>
        <span>www.qlinetelecom.com.au</span>
      </li>
    </ul>
    <p class="address">27 Marlow Street, Kelvin Grove, Brisbane</p>
    <div class="card__band"></div>
  </section>
</main>
</body>
</html>
```